Rebrand stationary with recently completed logo design

Need new business cards, thank you cards, letterhead, envelopes and presentation folders. The designs will be sent to a separate production firm so I need the files to be print ready.

My contact info
Reko Haliburn

Office 604-318-5047
Fax 604-371-8054

Email reko@glazemark.ca
website www.glazemark.ca

315-14720 62nd Avenue,
Langley, BC, V2K 3R8

Target Market(s)

Homeowners, businesses and contractors

Industry/Entity Type

Business

Font styles to use
Sans Serif

Colors
34a7d7

Requirements
Must have
• Like to have one side of the business card a solid color with the logo in all white. The side with all the text to be a white background
• I find the current blue on the front of the card with the white logo too dark.
Should not have
• Gradient colors

```html
<!DOCTYPE html>
<html lang="en">
<head>
<meta charset="utf-8">
<title>Glazemark Business Card</title>
<link href="https://fonts.googleapis.com/css2?family=Open+Sans:wght@400;600;700&family=PT+Sans+Narrow:wght@700&display=swap" rel="stylesheet">
<style>
  :root {
    --canvas: #e9e7e4;
    --card: #fbfbfb;
    --brand-blue: #34a7d7;
    --band-blue: #1c9bd8;
    --slate: #3f4e5a;
    --text: #555a5e;
    --text-strong: #3a3f44;
  }
  * { margin: 0; padding: 0; box-sizing: border-box; }
  html, body {
    width: 1200px; height: 960px; overflow: hidden;
    background: var(--canvas);
    font-family: "Open Sans", Arial, sans-serif;
  }
  .stage { position: relative; width: 1200px; height: 960px; }

  /* Front of card */
  .card-front {
    position: absolute; left: 302px; top: 130px;
    width: 600px; height: 340px;
    background: var(--card);
    box-shadow: 0 2px 6px rgba(0,0,0,.25);
  }
  .wordmark {
    font-family: "Open Sans", Arial, sans-serif;
    font-weight: 400; letter-spacing: 1px; line-height: 1;
  }
  .card-front .wordmark {
    position: absolute; right: 36px; top: 128px;
    font-size: 36px; color: var(--brand-blue);
  }
  .name-band {
    position: absolute; left: 0; top: 215px;
    width: 540px; height: 31px;
    background: var(--band-blue);
  }
  .name-band .holder-name {
    position: absolute; left: 28px; top: 3px;
    font-family: "PT Sans Narrow", "Arial Narrow", sans-serif;
    font-weight: 700; font-size: 21px; color: #fff; letter-spacing: .3px;
  }
  .band-tail {
    position: absolute; left: 540px; top: 218px;
    width: 60px; height: 25px; background: var(--slate);
  }
  .contact-list {
    position: absolute; left: 30px; top: 264px;
    list-style: none; font-size: 13px; color: var(--text);
  }
  .contact-list li { display: flex; align-items: center; height: 19px; }
  .contact-list svg { width: 12px; height: 12px; margin-right: 8px; fill: var(--brand-blue); }
  .address {
    position: absolute; right: 34px; top: 264px;
    text-align: right; font-size: 13px; color: var(--text); font-style: normal;
  }
  .address span { display: block; height: 19px; line-height: 19px; }
  .address .website { font-weight: 700; color: var(--text-strong); letter-spacing: 1.6px; }

  /* Back of card */
  .card-back {
    position: absolute; left: 299px; top: 489px;
    width: 600px; height: 342px;
    background: #fff;
    box-shadow: 0 2px 6px rgba(0,0,0,.25);
  }
  .card-back .panel {
    position: absolute; left: 14px; top: 12px;
    width: 572px; height: 316px;
    background: var(--slate);
  }
  .card-back .wordmark {
    position: absolute; left: 0; right: 0; top: 138px;
    text-align: center; font-size: 46px; color: #fff;
  }
</style>
</head>
<body>
<main class="stage">

  <section class="card-front" aria-label="Business card front">
    <div class="wordmark">GLAZEMARK</div>

    <div class="name-band"><span class="holder-name">REKO HALIBURN</span></div>
    <div class="band-tail"></div>

    <ul class="contact-list">
      <li>
        <svg viewBox="0 0 24 24" aria-hidden="true"><path d="M6.6 10.8a15.1 15.1 0 0 0 6.6 6.6l2.2-2.2a1 1 0 0 1 1-.25 11.4 11.4 0 0 0 3.6.57 1 1 0 0 1 1 1V20a1 1 0 0 1-1 1A17 17 0 0 1 3 4a1 1 0 0 1 1-1h3.5a1 1 0 0 1 1 1c0 1.25.2 2.45.57 3.57a1 1 0 0 1-.25 1z"/></svg>
        604-318-5047
      </li>
      <li>
        <svg viewBox="0 0 24 24" aria-hidden="true"><path d="M7 2h10v5H7z M3 8h18a1 1 0 0 1 1 1v7h-4v-3H6v3H2V9a1 1 0 0 1 1-1z M7 14h10v8H7z"/></svg>
        604-371-8054
      </li>
      <li>
        <svg viewBox="0 0 24 24" aria-hidden="true"><path d="M2 5h20v14H2z M2 5l10 8 10-8" stroke="#fff" stroke-width="1.5"/></svg>
        reko@glazemark.ca
      </li>
    </ul>

    <address class="address">
      <span>315-14720 62nd Avenue</span>
      <span>Langley, BC, V2K 3R8</span>
      <span class="website">www.glazemark.ca</span>
    </address>
  </section>

  <section class="card-back" aria-label="Business card back">
    <div class="panel"></div>
    <div class="wordmark">GLAZEMARK</div>
  </section>

</main>
</body>
</html>
```